eCommerce website for a DIY shop & communal center

We need a website for a business called The Maple Bench. The Maple Bench is both a shop and communal establishment where people with shared interests, especially in DIY (Do It Yourself) and crafting, can gather to shop for & work on projects while sharing ideas, equipment, supplies and knowledge. The shop is both brick & motor and online. The physical communal space provides workstations, equipment, tools and supplies and expertise for DIY lovers to create their projects.

Target Market(s)

Middle & upper class DIY enthusiasts, creative hobbyists, budding artists & small business owners

Industry/Entity Type

DIY, Arts & Crafts

Coding

Coded - Design and coding required

Number of Pages Required

5+ page

Requirements
Must have
• Menus to include 1. home page (with about us, operating hours, contacts, location, meet the team); 2. Bench Activities (how to DIY at the Bench, booking, equipment & tools, house rules); 3. Bench Events (events in the Bench, offsite events); 4. Resources (FAQs, tutorials, blogs, eBooks) and 5. Online shop
Nice to have
• Branding guidelines eg logo colours (see attachment) to influence design. Tillpost shop. Booking feature for activities & events at the Bench.

```html
<!DOCTYPE html>
<html lang="en">
<head>
<meta charset="utf-8">
<title>Maple Bench – Home</title>
<link rel="stylesheet" href="https://fonts.googleapis.com/css2?family=Marcellus&family=Cormorant+Garamond:ital,wght@1,700&family=EB+Garamond:wght@400;500&family=Roboto:wght@400;500;700&display=swap">
<style>
:root{
  --ink:#1b1b1b;
  --text:#555049;
  --accent:#e0202b;
  --page:#f5f4f2;
  --hero:#e6e6e8;
  --sand:#efe6dc;
  --peach:#f0dccb;
  --card:#f2e3d6;
  --line:#cfc7bf;
  --muted:#d6d2cd;
  --white:#fff;
}
*{box-sizing:border-box;margin:0;padding:0}
html,body{width:1200px;height:4173px;overflow:hidden}
body{position:relative;background:var(--page);font-family:"EB Garamond",serif;color:var(--text)}
.abs{position:absolute}
.heading{font-family:"Marcellus",serif;color:var(--ink);font-weight:400}
.btn{position:absolute;background:var(--ink);color:var(--white);font-family:"EB Garamond",serif;font-size:17px;font-weight:500;display:flex;align-items:center;justify-content:center;letter-spacing:.3px}
.photo{position:absolute}

/* header */
.hero{position:absolute;left:0;top:0;width:1200px;height:685px;background:var(--hero)}
.hero-photo{left:470px;top:80px;width:730px;height:605px;background:radial-gradient(ellipse at 60% 55%,#c59a66 0%,#e7a34a 22%,#d9d3c9 52%,var(--hero) 75%)}
.logo{left:110px;top:36px;font-family:"Marcellus",serif;font-size:30px;color:var(--ink)}
.nav{left:370px;top:47px;display:flex;gap:23px;font-size:14px;color:#333}
.nav .active{color:var(--accent);border-bottom:1px solid var(--accent);padding-bottom:4px}
.search{left:876px;top:46px;width:130px;border-bottom:1px solid #333;font-size:14px;color:#333;padding-bottom:2px}
.kicker{left:108px;top:246px;font-size:24px;color:var(--accent);font-family:"Marcellus",serif}
.hero-title{left:106px;top:275px;font-family:"Cormorant Garamond",serif;font-style:italic;font-weight:700;font-size:92px;color:var(--ink);line-height:1}
.hero-text{left:111px;top:384px;width:430px;font-size:15px;line-height:29px}
.dots{left:38px;top:314px}
.dots span{display:block;width:15px;height:15px;border:1.5px solid #333;border-radius:50%;margin-bottom:6px}
.dots .on{background:#333}

/* about */
.about-title{left:600px;top:870px;width:480px;text-align:center;font-size:44px}
.about-text{left:600px;top:936px;width:480px;text-align:center;font-size:15px;line-height:29px}

/* hours */
.sand-band{background:var(--sand)}
.hours-title{left:100px;top:1500px;width:450px;text-align:right;font-size:44px}
.hours-text{left:100px;top:1570px;width:450px;text-align:right;font-size:15px;line-height:29px}
.hours-side{left:30px;top:1449px;writing-mode:vertical-rl;font-size:34px;color:var(--muted);font-family:"EB Garamond",serif}

/* team */
.team{left:0;top:1969px;width:1200px;height:513px;background:var(--peach)}
.team-title{left:0;top:2012px;width:1200px;text-align:center;font-size:44px}
.member{position:absolute;top:2089px;width:235px;height:338px;background:var(--card);border:2px solid #d8c6b6}
.member .pic{position:absolute;left:6px;top:6px;width:219px;height:259px;background:linear-gradient(160deg,#8d8f94,#5f5a56)}
.member .badge{position:absolute;right:6px;top:6px}
.member .name{position:absolute;left:0;top:278px;width:100%;text-align:center;font-size:16px;color:var(--ink)}
.member .role{position:absolute;left:0;top:302px;width:100%;text-align:center;font-size:13px}
.arrow{position:absolute;top:2208px}

/* location */
.loc-title{left:640px;top:2680px;font-size:44px}
.loc-text{left:640px;top:2744px;width:430px;font-size:14.5px;line-height:29px}
.loc-card{left:640px;top:2817px;width:430px;height:159px;background:var(--white);box-shadow:0 2px 8px rgba(0,0,0,.12);font-family:"Roboto",sans-serif;font-size:14px;color:#333}
.loc-card .lname{position:absolute;left:21px;top:33px;font-family:"EB Garamond",serif;font-size:17px;color:var(--ink)}
.loc-card .addr{position:absolute;left:21px;top:62px;width:330px;line-height:24px}
.loc-card .phone{position:absolute;left:21px;top:118px;font-size:13px;display:flex;align-items:center;gap:5px}
.loc-card .dir{position:absolute;left:355px;top:53px;text-align:center;font-size:10.5px}

/* activities */
.activities{left:0;top:3181px;width:1200px;height:418px;background:linear-gradient(90deg,#4a4642 0%,#5e5852 45%,#7a7066 70%,#4b4540 100%)}
.act-title{left:50px;top:3268px;font-size:44px;color:var(--white)}
.act-text{left:50px;top:3337px;width:570px;font-size:15px;line-height:31px;color:#eee}

/* contact */
.field{position:absolute;left:112px;width:429px;height:54px;border:1px solid var(--line);border-radius:3px;background:var(--page);font-family:"Roboto",sans-serif;font-size:12.5px;color:#333;padding:20px 0 0 17px}
.contact-title{left:602px;top:3722px;font-size:34px}
.contact-text{left:605px;font-family:"Roboto",sans-serif;font-size:13.5px;color:#333}
.socials{left:606px;top:3952px;display:flex;gap:13px}
.socials span{width:26px;height:26px;border-radius:50%;background:var(--ink)}
.footer{left:600px;top:4005px;font-family:"Roboto",sans-serif;font-size:12.5px;color:#333}
</style>
</head>
<body>

<!-- Header & hero -->
<section class="hero" aria-label="Hero">
  <div class="photo hero-photo" role="img" aria-label="Rolls of coloured felt, scissors and tape measure in a burlap sack with a pincushion and thread spools"></div>
</section>
<div class="abs logo">Maple Bench</div>
<nav class="abs nav">
  <span class="active">Home</span><span>Bench Activities ▾</span><span>Bench Events ▾</span><span>Resources</span><span>Online Shop</span>
</nav>
<div class="abs search">Search <svg width="11" height="11" viewBox="0 0 12 12" style="float:right;margin-top:4px"><circle cx="5" cy="5" r="3.6" fill="none" stroke="#222" stroke-width="1.6"/><line x1="7.7" y1="7.7" x2="11" y2="11" stroke="#222" stroke-width="1.6"/></svg></div>
<svg class="abs" style="left:1033px;top:48px" width="14" height="16" viewBox="0 0 14 16"><circle cx="7" cy="4.5" r="3.8" fill="#222"/><path d="M0 16c0-5 3-7.5 7-7.5s7 2.5 7 7.5z" fill="#222"/></svg>
<svg class="abs" style="left:1064px;top:34px" width="22" height="32" viewBox="0 0 22 32"><circle cx="11" cy="7" r="7" fill="#333"/><text x="11" y="10" text-anchor="middle" font-size="8" fill="#fff" font-family="Roboto,sans-serif">0</text><path d="M3 18h16l-2 12H5z" fill="#222"/><path d="M7 18a4 4 0 0 1 8 0" fill="none" stroke="#222" stroke-width="1.6"/></svg>

<div class="abs dots"><span></span><span class="on"></span><span></span></div>
<div class="abs kicker">Maple Bench</div>
<h1 class="abs hero-title">Crafting</h1>
<p class="abs hero-text">Lorem ipsum dolor sit amet, consectetur adipiscing elit, sed do eiusmod tempor incididunt ut labore et dolore magna aliqua. Ut enim ad minim veniam, quis</p>
<a class="btn" style="left:112px;top:486px;width:184px;height:50px">SHOP NOW</a>

<!-- About -->
<div class="photo" style="left:112px;top:772px;width:228px;height:268px;background:linear-gradient(135deg,#b49776,#7a6450)" role="img" aria-label="Hands marking wood with a pencil and ruler"></div>
<div class="photo" style="left:250px;top:880px;width:335px;height:390px;background:#d9d6d2"></div>
<div class="photo" style="left:240px;top:873px;width:335px;height:397px;background:linear-gradient(150deg,#4e4038,#8a5a44 55%,#3b302a);box-shadow:0 3px 8px rgba(0,0,0,.25)" role="img" aria-label="Carpenter drawing a line on a wooden plank"></div>
<h2 class="abs heading about-title">About Us</h2>
<p class="abs about-text">Lorem ipsum dolor sit amet, consectetur adipiscing elit, sed do eiusmod tempor incididunt ut labore et dolore magna aliqua. Ut enim ad minim veniam, quis nostrud exercitation ullamco</p>
<a class="btn" style="left:748px;top:1043px;width:185px;height:51px">READ MORE</a>

<!-- Operating hours -->
<div class="abs sand-band" style="left:486px;top:1413px;width:714px;height:415px"></div>
<div class="photo" style="left:609px;top:1357px;width:414px;height:526px;background:linear-gradient(170deg,#6f6a66,#8c7a6a 50%,#5a4e47);box-shadow:0 3px 8px rgba(0,0,0,.2)" role="img" aria-label="Two women knitting at a table with a bowl of yarn"></div>
<div class="abs hours-side">Mon - Fri 9.00am To 6.30pm</div>
<h2 class="abs heading hours-title">Operating Hours</h2>
<p class="abs hours-text">Lorem ipsum dolor sit amet, consectetur adipiscing elit, sed do eiusmod tempor incididunt ut labore et dolore magna aliqua. Ut enim ad minim veniam, quis nostrud exercitation ullamcout.</p>
<a class="btn" style="left:332px;top:1682px;width:217px;height:51px">SEE WORK SCHEDULE</a>

<!-- Team -->
<section class="abs team" aria-label="Team"></section>
<h2 class="abs heading team-title">Meet The Team</h2>
<svg class="arrow" style="left:47px" width="36" height="36" viewBox="0 0 36 36"><rect x="1.5" y="1.5" width="33" height="33" fill="none" stroke="#222" stroke-width="3"/><path d="M23 10v16L11 18z" fill="#222"/></svg>
<svg class="arrow" style="left:1104px" width="36" height="36" viewBox="0 0 36 36"><rect x="1.5" y="1.5" width="33" height="33" fill="none" stroke="#222" stroke-width="3"/><path d="M13 10v16l12-8z" fill="#222"/></svg>

<div class="member" style="left:108px"><div class="pic" role="img" aria-label="Portrait of team member"></div><svg class="badge" width="66" height="66"><path d="M0 0h66v66z" fill="var(--accent)"/></svg><div class="name">Rowan Ellery</div><div class="role">Lorem ipsum</div></div>
<div class="member" style="left:356px"><div class="pic" style="background:linear-gradient(160deg,#b9b1a4,#77735d)" role="img" aria-label="Portrait of team member"></div><svg class="badge" width="66" height="66"><path d="M0 0h66v66z" fill="var(--accent)"/></svg><div class="name">Rowan Ellery</div><div class="role">Lorem ipsum</div></div>
<div class="member" style="left:605px"><div class="pic" style="background:linear-gradient(160deg,#3d3a36,#3e4a66)" role="img" aria-label="Portrait of team member"></div><svg class="badge" width="66" height="66"><path d="M0 0h66v66z" fill="var(--accent)"/></svg><div class="name">Rowan Ellery</div><div class="role">Lorem ipsum</div></div>
<div class="member" style="left:853px"><div class="pic" style="background:linear-gradient(160deg,#c9c0b2,#5a4640)" role="img" aria-label="Portrait of team member"></div><svg class="badge" width="66" height="66"><path d="M0 0h66v66z" fill="var(--accent)"/></svg><div class="name">Rowan Ellery</div><div class="role">Lorem ipsum</div></div>

<!-- Location -->
<div class="abs sand-band" style="left:0;top:2626px;width:711px;height:413px"></div>
<div class="photo" style="left:164px;top:2569px;width:414px;height:528px;background:linear-gradient(180deg,#55617a,#b7a58e 45%,#6b7666 80%,#4e6a45);box-shadow:0 3px 8px rgba(0,0,0,.2)" role="img" aria-label="City skyline with towers and an arched bridge"></div>
<h2 class="abs heading loc-title">Location</h2>
<p class="abs loc-text">Lorem ipsum dolor sit amet, consectetur adipiscing elit, eiusmod tempor incididunt ut labore et dolore magna aliqua.</p>
<div class="abs loc-card">
  <div class="lname">Maple Bench</div>
  <div class="addr"><b style="font-weight:500">Address -</b> 48 Alder Row, Millbrook, Westfold United States</div>
  <div class="phone"><svg width="11" height="11" viewBox="0 0 24 24"><path d="M6.6 10.8a15 15 0 0 0 6.6 6.6l2.2-2.2a1 1 0 0 1 1-.25 11.4 11.4 0 0 0 3.6.6 1 1 0 0 1 1 1V20a1 1 0 0 1-1 1A17 17 0 0 1 3 4a1 1 0 0 1 1-1h3.5a1 1 0 0 1 1 1 11.4 11.4 0 0 0 .6 3.6 1 1 0 0 1-.25 1z" fill="#222"/></svg>555-014-2290</div>
  <div class="dir"><svg width="48" height="48" viewBox="0 0 48 48"><circle cx="24" cy="24" r="24" fill="var(--accent)"/><path d="M14 23l20-8-8 20-3-9z" fill="#fff"/></svg><div>Get Direction</div></div>
</div>

<!-- Bench activities -->
<section class="abs activities" role="img" aria-label="Balls of yarn in a wicker basket on a dark wooden surface"></section>
<h2 class="abs heading act-title">Bench Activities</h2>
<p class="abs act-text">Lorem ipsum dolor sit amet, consectetur adipiscing elit, sed do eiusmod tempor incididunt ut labore et dolore magna aliqua. Ut enim ad minim veniam, quis nostrud exercitation ullamco laboris nisi ut aliquip ex ea commodo consequat.</p>
<a class="btn" style="left:53px;top:3449px;width:185px;height:50px">BOOK NOW</a>

<!-- Contact -->
<div class="field" style="top:3686px">First Nmae</div>
<div class="field" style="top:3754px">Last Name</div>
<div class="field" style="top:3823px">Email</div>
<div class="field" style="top:3890px">Subject</div>
<div class="field" style="top:3958px;height:90px">Message</div>
<a class="btn" style="left:112px;top:4063px;width:257px;height:53px;font-size:20px">SEND</a>

<h2 class="abs heading contact-title">Contact Us</h2>
<p class="abs contact-text" style="top:3781px">We'd love to hear from you, so why not drop us a message?</p>
<p class="abs contact-text" style="top:3815px">Our friendly team love to chat, so why not give us a</p>
<p class="abs contact-text" style="top:3839px;font-weight:700">Call On 555-014-2290</p>
<div class="abs socials"><span></span><span></span><span></span><span></span><span></span><span></span></div>
<p class="abs footer">© 2021 Maple Bench | All rights reserved | Terms &amp; Condtions</p>

</body>
</html>
```